Yoga class opening. Little schedule for JUNE JULY and AUGUST

Flyer to promote an opening yoga class. The color of the docx haven't to be respected.

We want something joyfull, professional, clean and serious.

About the logo we oppened a contest at the same time so at the moment there is no logo but the logo color will be simple.

The phone number will change so you can poste a random one for the design that i can change by myself.

i recieved many creation in both side BUT i want something in 1 side :)

Target Market(s)

Yoga student. all age

Industry/Entity Type

It Professional

Logo Text

Yoga fern

Font styles to use
Sans Serif

Requirements
Must have
• The text present on the docx
Nice to have
• Some symbols about yoga ( Namasté signs, mandala, ... )
Should not have
• Not too much details it has to be clear.

```html
<!DOCTYPE html>
<html lang="fr">
<head>
<meta charset="utf-8">
<title>Yoga fern – Flyer ouverture</title>
<link rel="stylesheet" href="https://fonts.googleapis.com/css2?family=Arimo:wght@400;700&family=Roboto+Condensed:wght@400;700&family=Lato:wght@400;700&display=swap">
<style>
  :root {
    --ink: #1b1b1b;
    --dark: #232323;
    --pink: #e2406b;
    --pink-deep: #c42a55;
    --gold: #f2a92a;
    --gold-deep: #e59a1c;
    --red-tag: #b8213f;
    --white: #ffffff;
    --paper: #f7f7f7;
    --sun-top: #f6b733;
    --sun-bottom: #5a3a0e;
  }
  html, body { margin: 0; padding: 0; width: 907px; height: 1200px; overflow: hidden; background: #e9e9e9; }
  .flyer { position: relative; width: 907px; height: 1200px; overflow: hidden; background: var(--paper); font-family: 'Arimo', Arial, sans-serif; color: var(--ink); }
  .backdrop { position: absolute; left: 0; top: 0; }
  .abs { position: absolute; margin: 0; }

  .brand { right: 29px; top: 28px; font-size: 42px; font-weight: 700; color: var(--gold); letter-spacing: 1px; text-align: right; }
  .nouveau { right: 29px; top: 96px; font-size: 31px; font-weight: 700; color: var(--gold); }
  .studio { right: 29px; top: 140px; text-align: right; color: var(--white); line-height: 1.2; }
  .studio .l1 { display: block; font-size: 31px; font-weight: 700; }
  .studio .l2 { display: block; font-size: 34px; font-weight: 400; }

  .opening { right: 29px; top: 330px; text-align: right; }
  .opening .label { display: block; font-size: 38px; color: var(--gold); }
  .opening .date { display: block; font-size: 46px; font-weight: 700; color: var(--white); margin-top: 2px; }
  .address { right: 29px; top: 448px; text-align: right; font-size: 18px; color: var(--white); line-height: 1.3; }

  .intro { left: 128px; top: 566px; font-size: 28px; line-height: 1.3; }
  .intro .pink { color: var(--pink); display: block; }
  .intro .dark { color: var(--ink); display: block; }

  .month-tag { position: absolute; left: 0; height: 28px; line-height: 28px; padding: 0 38px 0 26px; font-family: 'Roboto Condensed', sans-serif; font-weight: 700; font-size: 24px; color: var(--white); background: var(--red-tag); clip-path: polygon(0 0, 88% 0, 100% 50%, 88% 100%, 0 100%); }
  .month-tag.aout { background: var(--dark); color: var(--gold); left: 0; padding-left: 30px; }
  .course-title { position: absolute; left: 24px; font-family: 'Roboto Condensed', sans-serif; font-weight: 700; font-size: 16px; }
  .session { position: absolute; left: 24px; font-family: 'Roboto Condensed', sans-serif; font-size: 15px; white-space: nowrap; }
  .session .days { display: inline-block; width: 226px; font-weight: 700; color: var(--pink); font-size: 13.5px; }
  .aout-block .session .days { color: var(--ink); }
  .aout-block .course-title { color: var(--white); }

  .workshop { position: absolute; left: 676px; font-family: 'Roboto Condensed', sans-serif; }
  .workshop .title { font-weight: 700; font-size: 16px; line-height: 1.3; margin: 0 0 8px; }
  .workshop .slot { font-family: 'Lato', sans-serif; font-size: 14px; line-height: 23px; margin: 0; }

  .band-gold { left: 0; top: 987px; width: 907px; height: 183px; background: linear-gradient(180deg, var(--gold), var(--gold-deep)); }
  .band-foot { left: 0; top: 1166px; width: 907px; height: 34px; background: var(--dark); }

  .planning-box { left: 563px; top: 1002px; width: 305px; height: 103px; border-radius: 6px; background: linear-gradient(180deg, var(--pink), var(--pink-deep)); border: 2px solid #f5c14f; box-sizing: border-box; text-align: center; color: var(--white); font-family: 'Roboto Condensed', sans-serif; padding-top: 14px; }
  .planning-box .small { font-family: 'Lato', sans-serif; font-size: 14px; display: block; }
  .planning-box .big { font-weight: 700; font-size: 22px; display: block; line-height: 1.3; }
  .farewell { left: 563px; top: 1124px; width: 305px; text-align: center; font-size: 29px; color: var(--white); }

  .phone { left: 24px; top: 1166px; height: 34px; display: flex; align-items: center; gap: 8px; font-size: 26px; font-weight: 700; color: var(--white); }
  .social { right: 40px; top: 1166px; height: 34px; line-height: 34px; font-size: 15px; color: var(--pink); }
  .social strong { color: var(--white); font-weight: 700; }
</style>
</head>
<body>
<main class="flyer">
  <svg class="backdrop" width="907" height="1200" viewBox="0 0 907 1200">
    <defs>
      <linearGradient id="sky" x1="0" y1="0" x2="1" y2="1">
        <stop offset="0" stop-color="#2b2b2b"/>
        <stop offset="0.6" stop-color="#4a4a4a"/>
        <stop offset="1" stop-color="#1e1e1e"/>
      </linearGradient>
      <linearGradient id="rose" x1="0" y1="0" x2="1" y2="0">
        <stop offset="0" stop-color="#f0507a"/>
        <stop offset="1" stop-color="#c22b54"/>
      </linearGradient>
      <linearGradient id="sunset" x1="0" y1="0" x2="0" y2="1">
        <stop offset="0" stop-color="#f4a323"/>
        <stop offset="0.5" stop-color="#f8c84a"/>
        <stop offset="1" stop-color="#4e300b"/>
      </linearGradient>
    </defs>
    <polygon points="0,0 907,0 907,261 0,461" fill="url(#sky)"/>
    <polygon points="0,461 907,261 907,275 0,475" fill="var(--gold)"/>
    <polygon points="488,322 907,261 907,561 476,438" fill="url(#rose)"/>
    <polygon points="476,438 907,561 907,572 470,448" fill="var(--gold)"/>
    <g role="img" aria-label="Mandala ornament in gold and pink framing the photo">
      <circle cx="305" cy="285" r="262" fill="#d9a132"/>
    </g>
    <g role="img" aria-label="Photo of a person meditating in lotus pose at sunset by the sea">
      <circle cx="305" cy="285" r="178" fill="url(#sunset)" stroke="var(--dark)" stroke-width="6"/>
    </g>
  </svg>

  <h1 class="abs brand">YOGA FERN</h1>
  <p class="abs nouveau">NOUVEAU !!</p>
  <p class="abs studio"><span class="l1">VOTRE STUDIO DE</span><span class="l2">YOGA A IXELLES</span></p>

  <p class="abs opening"><span class="label">OUVERTURE LE</span><span class="date">6 JUIN 2016 AU</span></p>
  <p class="abs address">212 RUE DES TILLEULS<br>1050 IXELLES</p>

  <p class="abs intro"><span class="pink">En attendant le planning des cours de la rentrée,</span><span class="dark">YOGA FERN vous propose ses stages et ateliers d’été</span></p>

  <section class="juin-block">
    <div class="month-tag" style="top:645px">JUIN</div>
    <p class="course-title abs" style="top:679px">Stage découverte du YOGA 10h00 85 € :</p>
    <p class="session abs" style="top:718px"><span class="days">Du lundi 6 au vendredi 10 juin :</span>10h00 à 12h00 ou 18h00 à 20h00</p>
    <p class="session abs" style="top:741px"><span class="days">Du lundi 13 au vendredi 17 juin :</span>10h00 à 12h00 ou 18h00 à 20h00</p>
    <p class="session abs" style="top:764px"><span class="days">Du lundi 20 au vendredi 24 juin :</span>10h00 à 12h00 ou 18h00 à 20h00</p>
    <p class="session abs" style="top:787px"><span class="days">Du lundi 27 au vendredi 1er juillet :</span>10h00 à 12h00 ou 18h00 à 20h00</p>
  </section>

  <section class="juillet-block">
    <div class="month-tag" style="top:819px">JUILLET</div>
    <p class="course-title abs" style="top:853px">Stage initiation à l’ASHTANGA 10h00 85 €</p>
    <p class="session abs" style="top:878px"><span class="days">Du lundi 4 au vendredi 8 juillet :</span>10h00 à 12h00 ou 18h00 à 20h00</p>
    <p class="session abs" style="top:901px"><span class="days">Du lundi 11 au vendredi 15 juillet :</span>10h00 à 12h00 ou 18h00 à 20h00</p>
    <p class="session abs" style="top:924px"><span class="days">Du lundi 18 au vendredi 22 juillet :</span>10h00 à 12h00 ou 18h00 à 20h00</p>
    <p class="session abs" style="top:947px"><span class="days">Du lundi 25 au vendredi 29 juillet :</span>10h00 à 12h00 ou 18h00 à 20h00</p>
  </section>

  <div class="abs band-gold"></div>
  <div class="abs band-foot"></div>

  <section class="aout-block">
    <div class="month-tag aout" style="top:995px">AOUT</div>
    <p class="course-title abs" style="top:1030px">Stage découverte du YOGA 10h00 85 €</p>
    <p class="session abs" style="top:1060px"><span class="days">Du lundi 1er au vendredi 5 août :</span>10h00 à 12h00 ou 18h00 à 20h00</p>
    <p class="session abs" style="top:1083px"><span class="days">Du lundi 8 au vendredi 12 août :</span>10h00 à 12h00 ou 18h00 à 20h00</p>
    <p class="session abs" style="top:1106px"><span class="days">Du lundi 15 au vendredi 19 août :</span>10h00 à 12h00 ou 18h00 à 20h00</p>
    <p class="session abs" style="top:1129px"><span class="days">Du lundi 22 au vendredi 26 août :</span>10h00 à 12h00 ou 18h00 à 20h00</p>
  </section>

  <section class="workshop" style="top:670px">
    <p class="title">Atelier gestion du stress yoga/sophrologie<br>2h00 28 €</p>
    <p class="slot">Samedi 11 juin 10h30 à 12h30</p>
    <p class="slot">Samedi 11 juin 15h à 17h00</p>
    <p class="slot">Dimanche 12 juin 10h30 à 12h30</p>
    <p class="slot">Dimanche 12 juin 14h à 16h00</p>
  </section>
  <section class="workshop" style="top:840px">
    <p class="title">Atelier gestion du stress yoga/sophrologie<br>2h00 28 €</p>
    <p class="slot">Samedi 9 juillet 10h30 à 12h30</p>
    <p class="slot">Samedi 9 juillet 15h00 à 17h00</p>
    <p class="slot">Dimanche 10 juillet 10h30 à 12h30</p>
    <p class="slot">Dimanche 10 juillet 14h00 à 16h00</p>
  </section>

  <div class="abs planning-box">
    <span class="small">Démarrage du planning annuel le</span>
    <span class="big">5 septembre 2016</span>
    <span class="big">Plus d’info et inscription</span>
  </div>
  <p class="abs farewell">UN BEL ETE A TOUS !</p>

  <p class="abs phone">
    <svg width="20" height="20" viewBox="0 0 20 20" aria-hidden="true"><rect width="20" height="20" rx="4" fill="var(--pink)"/><path d="M6 4l2.5 0 1 3-1.5 1.2c.8 1.6 2 2.8 3.6 3.6L12.8 10.3l3 1V14c0 .8-.6 1.3-1.4 1.2C8.6 14.6 5.4 11.4 4.8 5.6 4.7 4.7 5.2 4 6 4z" fill="var(--white)"/></svg>
    0198765432
  </p>
  <p class="abs social">Ou via notre page Linkora : <strong>yoga fern</strong></p>
</main>
</body>
</html>
```